Business Card Design Project

- makeup artist business card

- original and creative

- Elegant design

- Feel free to come out with cool designs but stick to being elegant and attractive

- Design relates to makeup

- includes name, occupation, contact numbers, email, website

- regular size business card

- round corner card

- double sided

- on 1 side it should just have the website name in the center " moonveilstudio.net "

Industry/Entity Type

Business

Requirements
Must have
• Delia Marsh
Makeup Artist
USA: +1 (415)772-0461
Singapore: +65 82307915
deliamarsh@moonveilstudio.net
www.moonveilstudio.net
Should not have
• nothing cartoon looking.
Pictures of makeup being grab from the internet.. Examples: eyes or lips.

```html
<!DOCTYPE html>
<html lang="en">
<head>
<meta charset="utf-8">
<title>Delia Marsh – Makeup Artist Business Card</title>
<link rel="stylesheet" href="https://fonts.googleapis.com/css2?family=Arimo:wght@400&display=swap">
<style>
  :root {
    --page-bg: #ecebee;
    --front-tint: #c68bb0;
    --front-tint-deep: #b87aa2;
    --back-tint: #9a1d6b;
    --back-tint-deep: #861458;
    --front-ink: #3a2a34;
    --front-name: #ffffff;
    --role-ink: #1f1a1d;
    --back-ink: #ffffff;
    --silver-light: #f4f4f6;
    --silver-mid: #b9b9c0;
    --silver-dark: #6e6e76;
    --band-warm: #c9a07a;
    --band-mid: #cfa9a6;
    --band-cool: #a98aa8;
    --card-w: 780px;
    --card-h: 446px;
  }
  * { box-sizing: border-box; margin: 0; padding: 0; }
  html, body {
    width: 1067px;
    height: 1200px;
    overflow: hidden;
    background: var(--page-bg);
    font-family: "Arimo", Arial, sans-serif;
  }
  .canvas {
    position: relative;
    width: 1067px;
    height: 1200px;
  }
  .card {
    position: absolute;
    left: 143px;
    width: var(--card-w);
    height: var(--card-h);
    border-radius: 26px;
    overflow: hidden;
    box-shadow: 0 10px 28px rgba(60, 30, 50, 0.22);
  }
  .card--front {
    top: 110px;
    background: linear-gradient(180deg, var(--front-tint) 0%, var(--front-tint-deep) 100%);
    color: var(--front-ink);
  }
  .card--back {
    top: 644px;
    background: linear-gradient(180deg, var(--back-tint) 0%, var(--back-tint-deep) 100%);
    color: var(--back-ink);
  }
  .photo-band {
    position: absolute;
    top: 138px;
    left: 0;
    width: 100%;
    height: 144px;
  }
  .silver-rule {
    position: absolute;
    left: 0;
    width: 100%;
    height: 12px;
    background: linear-gradient(180deg, var(--silver-light) 0%, var(--silver-mid) 50%, var(--silver-dark) 100%);
  }
  .silver-rule--top { top: 0; }
  .silver-rule--bottom { bottom: 0; }
  .photo-band__fill {
    position: absolute;
    top: 12px;
    left: 0;
    width: 100%;
    height: 120px;
    background: linear-gradient(90deg, var(--band-warm) 0%, var(--band-mid) 30%, var(--band-cool) 50%, var(--band-mid) 70%, var(--band-warm) 100%);
  }
  .identity {
    position: absolute;
    top: 42px;
    left: 34px;
  }
  .identity__name {
    font-size: 30px;
    font-weight: 400;
    color: var(--front-name);
    letter-spacing: 0.5px;
    word-spacing: 8px;
  }
  .identity__role {
    margin-top: 6px;
    margin-left: 74px;
    font-size: 17px;
    color: var(--role-ink);
    word-spacing: 4px;
  }
  .web-contact {
    position: absolute;
    top: 34px;
    right: 34px;
    text-align: right;
    font-size: 19px;
    line-height: 32px;
    color: var(--front-ink);
  }
  .phone-list {
    position: absolute;
    top: 336px;
    left: 34px;
    font-size: 19px;
    line-height: 36px;
    color: var(--front-ink);
    list-style: none;
  }
  .phone-list__label { word-spacing: 4px; }
  .phone-list__number { margin-left: 8px; word-spacing: 4px; }
  .site-title {
    position: absolute;
    top: 46px;
    left: 0;
    width: 100%;
    text-align: center;
    font-size: 40px;
    font-weight: 400;
    color: var(--back-ink);
    letter-spacing: 0.3px;
  }
</style>
</head>
<body>
<main class="canvas">

  <section class="card card--front" aria-label="Business card front">
    <div class="identity">
      <h1 class="identity__name">Delia Marsh</h1>
      <p class="identity__role">Makeup Artist</p>
    </div>
    <div class="web-contact">
      <p class="web-contact__email">deliamarsh@moonveilstudio.net</p>
      <p class="web-contact__site">www.moonveilstudio.net</p>
    </div>
    <div class="photo-band">
      <div class="silver-rule silver-rule--top"></div>
      <div class="photo-band__fill" role="img" aria-label="Photograph strip showing a close-up of makeup work"></div>
      <div class="silver-rule silver-rule--bottom"></div>
    </div>
    <ul class="phone-list">
      <li><span class="phone-list__label">Phone USA:</span><span class="phone-list__number">+1 (415)772-0461</span></li>
      <li><span class="phone-list__label">Phone Singapore:</span><span class="phone-list__number">+65 82307915</span></li>
    </ul>
  </section>

  <section class="card card--back" aria-label="Business card back">
    <p class="site-title">www.moonveilstudio.net</p>
    <div class="photo-band">
      <div class="silver-rule silver-rule--top"></div>
      <div class="photo-band__fill" role="img" aria-label="Photograph strip showing a close-up of makeup work"></div>
      <div class="silver-rule silver-rule--bottom"></div>
    </div>
  </section>

</main>
</body>
</html>
```